Income Tax Flyer - Updates Needed

Just need to update this flyer design and give it a new look. We would like to keep all the same wording but make it stand out a little more. Our selling point is the "Same Day Tax Advance up to $6,000"

Lending, Small Loans, Tax Services, Title Loans, Personal Loans

```html
<!DOCTYPE html>
<html lang="en">
<head>
<meta charset="utf-8">
<title>Same Day Tax Advance Flyer</title>
<link href="https://fonts.googleapis.com/css2?family=Lato:wght@400;700;900&display=swap" rel="stylesheet">
<style>
  :root {
    --red: #c41f27;
    --red-deep: #9e161d;
    --green-dark: #0f5130;
    --green-bright: #0e8c43;
    --ink: #1c1c1c;
    --white: #ffffff;
    --mint: #d3e3da;
    --mint-soft: #eef5f1;
  }
  * { margin: 0; padding: 0; box-sizing: border-box; }
  html, body { width: 927px; height: 1200px; overflow: hidden; background: var(--white); }
  body { font-family: "Lato", sans-serif; color: var(--ink); }
  .flyer { position: relative; width: 927px; height: 1200px; overflow: hidden; background: var(--white); }

  .hero-photo { position: absolute; left: 0; top: 0; width: 927px; height: 620px; }

  .brand { position: absolute; left: 40px; top: 40px; color: var(--green-dark); font-weight: 700; line-height: 1; }
  .brand-name { display: block; font-size: 38px; }
  .brand-sub { display: block; font-size: 11px; letter-spacing: 3px; margin-top: 6px; }

  .offer {
    position: absolute; left: 40px; top: 150px; width: 520px; height: 340px;
    background: var(--red); color: var(--white);
    box-shadow: 14px 14px 0 var(--green-dark);
    padding: 34px 40px 0;
    font-weight: 900; line-height: 1;
  }
  .offer-kicker { display: block; font-size: 52px; letter-spacing: -0.5px; }
  .offer-kicker + .offer-kicker { margin-top: 6px; }
  .offer-rule { display: block; width: 90px; height: 6px; background: var(--white); margin: 22px 0 18px; }
  .offer-upto { display: block; font-size: 30px; letter-spacing: 2px; }
  .offer-amount { display: block; font-size: 104px; letter-spacing: -2px; margin-top: 2px; }

  .apply { position: absolute; left: 0; top: 638px; width: 927px; text-align: center; font-weight: 900; line-height: 1.1; }
  .apply-lead { color: var(--green-dark); font-size: 40px; letter-spacing: -0.3px; }
  .apply-amount { color: var(--red); font-size: 52px; letter-spacing: -1px; margin-top: 4px; }
  .apply-bar { display: block; width: 120px; height: 5px; background: var(--green-bright); margin: 16px auto 0; }

  .perks { position: absolute; left: 0; top: 810px; width: 927px; height: 190px; }
  .pitch { position: absolute; left: 40px; top: 40px; width: 230px; font-size: 25px; line-height: 38px; color: var(--green-dark); font-weight: 700; }

  .feature {
    position: absolute; top: 0; width: 190px; height: 190px;
    background: var(--mint-soft); border-top: 5px solid var(--green-dark);
    text-align: center; padding-top: 22px;
  }
  .feature svg { width: 64px; height: 64px; display: block; margin: 0 auto; }
  .feature-label { margin-top: 16px; font-size: 20px; line-height: 28px; }
  .feature--247 { left: 290px; }
  .feature--amount { left: 496px; }
  .feature--quick { left: 702px; }

  .contact { position: absolute; left: 0; top: 1035px; width: 927px; height: 165px; display: flex; }
  .contact-call { width: 288px; background: var(--red); color: var(--white); font-weight: 900; font-size: 30px; line-height: 42px; padding: 42px 0 0 40px; }
  .contact-info { flex: 1; background: var(--green-dark); color: var(--white); position: relative; }
  .contact-item { position: absolute; top: 40px; font-weight: 700; font-size: 22px; line-height: 33px; }
  .contact-item svg { position: absolute; left: -44px; top: 2px; width: 28px; height: 30px; }
  .contact-item--phone { left: 110px; }
  .contact-item--visit { left: 398px; }
  .code { position: absolute; right: 8px; bottom: 4px; font-size: 11px; color: var(--white); font-family: Arial, sans-serif; }
</style>
</head>
<body>
<main class="flyer">
  <svg class="hero-photo" viewBox="0 0 927 620">
    <defs>
      <linearGradient id="photoTone" x1="0" y1="0" x2="0.5" y2="1">
        <stop offset="0" stop-color="#e6e1da"/>
        <stop offset="0.55" stop-color="#d8c5aa"/>
        <stop offset="1" stop-color="#c48d57"/>
      </linearGradient>
    </defs>
    <path d="M470 0 H927 V600 H640 C500 560 420 420 430 260 C436 150 452 60 470 0 Z" fill="url(#photoTone)" role="img" aria-label="Photo of a couple reviewing tax papers together at a kitchen counter"/>
    <path d="M458 0 C440 60 424 150 418 260 C408 430 492 572 632 612" fill="none" stroke="var(--green-bright)" stroke-width="10"/>
    <path d="M470 0 C452 60 436 150 430 260 C420 420 500 560 640 600" fill="none" stroke="var(--green-dark)" stroke-width="6"/>
  </svg>

  <div class="brand">
    <span class="brand-name">Ledgerline</span>
    <span class="brand-sub">FINANCIAL GROUP</span>
  </div>

  <section class="offer">
    <span class="offer-kicker">SAME DAY</span>
    <span class="offer-kicker">TAX ADVANCE</span>
    <span class="offer-rule"></span>
    <span class="offer-upto">UP TO</span>
    <span class="offer-amount">$6,000</span>
  </section>

  <section class="apply">
    <div class="apply-lead">APPLY HERE FOR</div>
    <div class="apply-amount">$5,000-$6,000 TODAY!</div>
    <span class="apply-bar"></span>
  </section>

  <section class="perks">
    <p class="pitch">File your taxes &amp;<br>apply for an Easy<br>Advance!</p>

    <div class="feature feature--247">
      <svg viewBox="0 0 72 72">
        <circle cx="46" cy="50" r="16" fill="var(--mint)"/>
        <circle cx="34" cy="34" r="31" fill="none" stroke="var(--green-dark)" stroke-width="2" stroke-dasharray="2 3"/>
        <circle cx="36" cy="34" r="24" fill="none" stroke="var(--green-dark)" stroke-width="3"/>
        <path d="M52 12 l4 -5 l1 7z" fill="var(--green-dark)"/>
        <text x="36" y="40" text-anchor="middle" font-family="Lato, sans-serif" font-weight="900" font-size="16" fill="var(--green-dark)">24/7</text>
      </svg>
      <div class="feature-label">Available in 24<br>Hours or Less</div>
    </div>

    <div class="feature feature--amount">
      <svg viewBox="0 0 72 72">
        <circle cx="46" cy="52" r="15" fill="var(--mint)"/>
        <circle cx="36" cy="36" r="16" fill="none" stroke="var(--green-dark)" stroke-width="3"/>
        <text x="36" y="43" text-anchor="middle" font-family="Lato, sans-serif" font-weight="700" font-size="20" fill="var(--green-dark)">$</text>
        <path d="M20 14 q14 -10 30 -4 h12" fill="none" stroke="var(--green-dark)" stroke-width="3"/>
        <rect x="62" y="2" width="7" height="16" fill="none" stroke="var(--green-dark)" stroke-width="3"/>
        <path d="M52 58 q-14 10 -30 4 h-12" fill="none" stroke="var(--green-dark)" stroke-width="3"/>
        <rect x="3" y="54" width="7" height="16" fill="none" stroke="var(--green-dark)" stroke-width="3"/>
      </svg>
      <div class="feature-label">Choose your Loan<br>Amount</div>
    </div>

    <div class="feature feature--quick">
      <svg viewBox="0 0 72 72">
        <circle cx="52" cy="52" r="15" fill="var(--mint)"/>
        <circle cx="42" cy="40" r="24" fill="none" stroke="var(--green-dark)" stroke-width="3"/>
        <rect x="38" y="6" width="10" height="6" fill="none" stroke="var(--green-dark)" stroke-width="3"/>
        <path d="M43 12 v4 M42 40 l-6 -10 M42 40 l12 4" stroke="var(--green-dark)" stroke-width="3" fill="none"/>
        <path d="M2 26 h12 M6 34 h8 M2 42 h10 M8 50 h8" stroke="var(--green-dark)" stroke-width="2"/>
      </svg>
      <div class="feature-label">Quick and<br>Easy</div>
    </div>
  </section>

  <footer class="contact">
    <div class="contact-call">CONTACT US<br>TODAY!</div>
    <div class="contact-info">
      <div class="contact-item contact-item--phone">
        <svg viewBox="0 0 24 24"><path fill="var(--white)" d="M6.6 10.8c1.4 2.8 3.8 5.1 6.6 6.6l2.2-2.2c.3-.3.7-.4 1-.2 1.1.4 2.3.6 3.6.6.6 0 1 .4 1 1V20c0 .6-.4 1-1 1C10.6 21 3 13.4 3 4c0-.6.4-1 1-1h3.5c.6 0 1 .4 1 1 0 1.3.2 2.5.6 3.6.1.3 0 .7-.2 1z"/></svg>
        Call Us:<br>+1 800-555-0142
      </div>
      <div class="contact-item contact-item--visit">
        <svg viewBox="0 0 24 26"><path fill="var(--white)" d="M12 1a8 8 0 0 0-8 8c0 6 8 16 8 16s8-10 8-16a8 8 0 0 0-8-8zm0 11a3 3 0 1 1 0-6 3 3 0 0 1 0 6z"/></svg>
        Visit Us:<br>Ledgerline,<br>Address comes here
      </div>
      <span class="code">C50</span>
    </div>
  </footer>
</main>
</body>
</html>
```